Business card design for my company.
I would like the card's background colour to be black. You can also see our web site to get an idea of our brand. https://www.tmwhomecrafting.com.au/
- Name
- Email

```html
<!DOCTYPE html>
<html lang="en">
<head>
<meta charset="utf-8">
<title>TMW Home Crafting – Business Card</title>
<link rel="stylesheet" href="https://fonts.googleapis.com/css2?family=Montserrat:wght@400;500;700&display=swap">
<style>
  :root {
    --stage: #3a3a3a;
    --card: #222222;
    --card-band: #2a2a2a;
    --green: #1e9b4a;
    --white: #f2f2f2;
    --muted: #d9d9d9;
  }
  * { margin: 0; padding: 0; box-sizing: border-box; }
  html, body {
    width: 1200px; height: 875px; overflow: hidden;
    background: var(--stage);
    font-family: "Montserrat", sans-serif;
  }
  .stage {
    position: relative; width: 1200px; height: 875px;
    display: flex; align-items: center; justify-content: center; gap: 40px;
  }
  .card {
    position: relative; width: 540px; height: 309px;
    background: var(--card); border-radius: 16px; overflow: hidden;
    box-shadow: 0 18px 40px rgba(0,0,0,.45);
  }
  .brand {
    display: flex; align-items: center; gap: 12px;
    color: var(--white); font-weight: 700; letter-spacing: .08em;
    text-transform: uppercase; white-space: nowrap;
  }
  .brand-mark { width: 14px; height: 14px; background: var(--green); flex: none; }
  .card-front .brand {
    position: absolute; inset: 0; justify-content: center; font-size: 30px;
  }
  .card-front .brand-mark { width: 22px; height: 22px; }
  .back-band { position: absolute; inset: 0; }
  .card-back .brand {
    position: absolute; left: 34px; bottom: 54px; font-size: 19px;
  }
  .contact { position: absolute; left: 290px; top: 56px; }
  .person-name {
    color: var(--green); font-weight: 700; font-size: 20px;
    letter-spacing: .04em; text-transform: uppercase;
  }
  .person-role { color: var(--white); font-size: 13px; margin-top: 4px; }
  .divider { width: 14px; height: 2px; background: var(--green); margin: 16px 0 12px; }
  .contact-list { list-style: none; }
  .contact-list li {
    display: flex; align-items: center; gap: 8px;
    color: var(--muted); font-size: 11.5px; margin-bottom: 8px; white-space: nowrap;
  }
  .contact-list svg { width: 11px; height: 11px; flex: none; }
</style>
</head>
<body>
<main class="stage">
  <section class="card card-front" aria-label="Business card front">
    <div class="brand"><span class="brand-mark"></span>TMW Home Crafting</div>
  </section>

  <section class="card card-back" aria-label="Business card back">
    <svg class="back-band" viewBox="0 0 540 309" preserveAspectRatio="none" aria-hidden="true">
      <polygon points="250,309 470,70 540,70 540,309" fill="var(--card-band)"/>
    </svg>
    <div class="brand"><span class="brand-mark"></span>TMW Home Crafting</div>
    <div class="contact">
      <h1 class="person-name">Darren Hale</h1>
      <p class="person-role">CEO/Founder</p>
      <div class="divider"></div>
      <ul class="contact-list">
        <li>
          <svg viewBox="0 0 12 12" aria-hidden="true"><path d="M2.5 1 L4.5 1 L5.2 3.6 L4 4.6 Q5 7 7.4 8 L8.4 6.8 L11 7.5 L11 9.5 Q11 11 9.5 11 Q1 10 1 2.5 Q1 1 2.5 1Z" fill="var(--green)"/></svg>
          897-555-0142
        </li>
        <li>
          <svg viewBox="0 0 12 12" aria-hidden="true"><rect x="0.5" y="2" width="11" height="8" fill="var(--green)"/><path d="M0.5 2 L6 6.5 L11.5 2" stroke="var(--card)" stroke-width="1" fill="none"/></svg>
          info@tmwhomecrafting.com.au
        </li>
        <li>
          <svg viewBox="0 0 12 12" aria-hidden="true"><circle cx="6" cy="6" r="5.3" fill="var(--green)"/><path d="M0.7 6 H11.3 M6 0.7 V11.3 M6 0.7 Q2.5 6 6 11.3 M6 0.7 Q9.5 6 6 11.3" stroke="var(--card)" stroke-width=".8" fill="none"/></svg>
          www.tmwhomecrafting.com.au
        </li>
      </ul>
    </div>
  </section>
</main>
</body>
</html>
```